Geschäftspapiere für Fliesenleger - Meisterbetrieb
Zielgruppe
Wir sind ein mittelständischer Fliesenleger - Meisterbetrieb und möchten unsere Geschäftspapiere erneuern. Unsere Kunden sind Privatkunden, Gewerbetreibende sowie Öffentliche Auftraggeber.
Aufgabenstellung
Unser Logo stellen wir Ihnen zur verfügung und soll unverändert bleiben.
Wir benötigen folgende Geschäftspapiere:
- Briefpapier DIN A4
- Notizblock Karriert DIN A4
- Visitenkarten 5,5 x 8,5 cm
- Kuvert DIN lang mit Fenster
- Kuvert DIN C4 mit Fenster
Bei der Farbe Rot handelt es sich um Verkehrsrot RAL 3020
Als Schriftart haben wir uns Helvetica Neue vorgestellt.
Wir bitten jedoch auch um Vorschläge anderer Moderner und gut lesbarer Schriftarten die für Print und Web bestens geeignet sind.
Wir wünschen uns ein Modernes und Schnörkelloses Design. Bei den Dateien habe ich Ihnen ein Stockphoto angehängt um Ihnen zu zeigen wie wir uns ein Cover oder eine Broschüre vorstellen können. Nur um Ihnen unsere Ideen / Vorstellungen näher zu bringen.

```html
<!DOCTYPE html>
<html lang="de">
<head>
<meta charset="utf-8">
<title>Briefpapier Fliesen-Korbel</title>
<link rel="stylesheet" href="https://fonts.googleapis.com/css2?family=Inter:wght@400;700;800&display=swap">
<style>
  :root {
    --ink: #1a1a1a;
    --red: #cc0a14;
    --rule: #333333;
    --paper: #ffffff;
    --backdrop: #f1f1f1;
  }
  * { margin: 0; padding: 0; box-sizing: border-box; }
  html, body { width: 1071px; height: 1200px; overflow: hidden; background: var(--backdrop); }
  body { font-family: "Inter", Helvetica, Arial, sans-serif; color: var(--ink); }
  .sheet {
    position: absolute; left: 111px; top: 0;
    width: 849px; height: 1200px; background: var(--paper);
  }
  .abs { position: absolute; }
  .brand {
    left: 560px; top: 92px; width: 222px; text-align: right;
    font-size: 31px; font-weight: 800; letter-spacing: -0.5px; color: var(--ink);
  }
  .sender-line { left: 69px; top: 115px; font-size: 9px; word-spacing: 1px; }
  .sender-line span { margin-right: 12px; }
  .recipient, .contact, .footer-info { font-size: 12.5px; line-height: 15.4px; }
  .recipient { left: 69px; top: 204px; }
  .contact, .footer-info { left: 561px; border-left: 1px solid var(--rule); padding-left: 9px; }
  .contact { top: 206px; height: 121px; top: 206px; padding-top: 0; }
  .contact p + p, .footer-info p + p { margin-top: 15px; }
  .footer-info { top: 1010px; height: 121px; }
  .meta { left: 71px; top: 367px; width: 710px; display: flex; justify-content: space-between;
    font-size: 12.5px; font-weight: 700; }
  .fold-mark { left: 0; width: 19px; height: 1px; background: var(--rule); }
  .letter { left: 72px; width: 702px; font-size: 12.5px; line-height: 15.4px; }
  .salutation { top: 477px; }
  .body-text { top: 538px; }
  .closing { top: 691px; }
  .tile-band { left: 0; top: 1000px; width: 330px; height: 118px;
    background: linear-gradient(90deg, #555 0%, #2a2a2a 40%, #d9303b 75%, #777 100%); opacity: .85; }
</style>
</head>
<body>
<div class="sheet">
  <div class="abs brand">Fliesen-Korbel</div>

  <div class="abs sender-line"><span>KRBL Korbel GmbH</span><span>Unterlindach 14</span><span>91380 Waldheim</span></div>

  <address class="abs recipient" style="font-style:normal">
    Frau Susanne Muster<br>Dorfstraße 121<br>91380 Waldheim
  </address>

  <div class="abs contact">
    <p>KRBL Korbel GmbH<br>Unterlindach 14<br>91380 Waldheim</p>
    <p>Tel.: 09188-4417230<br>Fax: 09188-4417239<br>Email: post@fliesen-korbel.de<br>Web: www.fliesen-korbel.de</p>
  </div>

  <div class="abs meta"><span>Rechnungsnr.:</span><span>Waldheim, 06.Mai 2025</span></div>

  <div class="abs fold-mark" style="top:423px"></div>
  <div class="abs fold-mark" style="top:599px"></div>

  <p class="abs letter salutation">Sehr geehrte Frau Muster,</p>
  <p class="abs letter body-text">Lorem ipsum dolor sit amet, consectetuer adipiscing elit, sed diam nonummy nibh euismod tincidunt ut laoreet dolore magna aliquam erat volutpat. Ut wisi enim ad minim veniam, quis nostrud exerci tation ullamcorper suscipit lobortis nisl ut aliquip ex ea commodo consequat. Duis autem vel eum iriure dolor in hendrerit in vulputate velit esse molestie consequat, vel illum dolore eu feugiat nulla facilisis at vero eros et accumsan et iusto odio dignissim qui blandit praesent luptatum zzril delenit augue duis dolore te feugait nulla facilisi.<br>Lorem ipsum dolor sit amet, cons ectetuer adipiscing elit, sed diam nonummy nibh euismod tincidunt ut laoreet dolore magna aliquam erat volutpat. Ut wisi enim ad minim veniam, quis nostrud exerci tation ullamcorper suscipit lobortis nisl ut aliquip ex ea commodo consequat.</p>
  <p class="abs letter closing">Mit freundlichen Grüßen</p>

  <div class="abs tile-band" role="img" aria-label="Dekoratives Muster aus abgerundeten Fliesenstreifen in Schwarz, Grau und Rot"></div>

  <div class="abs footer-info">
    <p>Bankverbindung:<br>Talbank Mittelfranken<br>IBAN: DE00 0000 0000 0000 0000 00<br>BIC: TALBDEF1WLD</p>
    <p>Geschäftsführer: Gerd Ulko<br>HRB 4471 Amtsgericht Talstadt<br>Ust. ID: DE204719586</p>
  </div>
</div>
</body>
</html>
```